Professional Package for CPA Firm

We would like a stationery design for our new CPA Firm based in Atlanta, GA called 'Vale 8'. We work with investors to help grow investments, tax free. We would like the design to have a professional/minimal look with a 'wow' factor. We need 9.5″ x 4.125″, 9x12, and 10x13 mailing envelopes, business cards, and a letterhead. We have a logo that is already complete. For the letterhead, we would like to have space to put credentials at the bottom of the page

Industry/Entity Type

CPA, Accounting

```html
<!DOCTYPE html>
<html lang="en">
<head>
<meta charset="utf-8">
<title>Vale 8 Stationery Package</title>
<link rel="stylesheet" href="https://fonts.googleapis.com/css2?family=Open+Sans:wght@400;600;700&family=Lato:wght@400&family=Montserrat:wght@300&family=Great+Vibes&display=swap">
<style>
:root{
  --stage:#8f8f8f;
  --ink:#1e1e20;
  --blue:#079bd8;
  --blue-text:#1a9fdc;
  --white:#ffffff;
  --body:#6a6a6a;
  --label:#1b1b1b;
}
*{margin:0;padding:0;box-sizing:border-box}
html,body{width:1200px;height:680px;overflow:hidden;background:var(--stage)}
body{position:relative;font-family:"Open Sans",Arial,sans-serif;color:var(--white)}
.piece{position:absolute}
.label{position:absolute;font-family:"Lato",Arial,sans-serif;font-size:9.5px;color:var(--label);letter-spacing:.2px;transform:translateX(-50%);white-space:nowrap}
.wordmark{display:flex;align-items:center;gap:4px;font-weight:700;color:var(--white);white-space:nowrap}
.wordmark .dot{background:var(--blue);display:block}
.script{font-family:"Great Vibes",cursive;white-space:nowrap}
.contact{list-style:none}
.contact li{display:flex;align-items:center;white-space:nowrap}
.contact svg{fill:var(--blue);flex:none}
.name{color:var(--blue-text);font-weight:600;white-space:nowrap}
.rule-v{position:absolute;width:1px;background:rgba(255,255,255,.35)}

/* letterhead */
.letterhead{left:66px;top:47px;width:391px;height:553px;background:var(--white);overflow:hidden}
.letterhead .band{height:103px;background:var(--ink);position:relative}
.letterhead .wordmark{position:absolute;left:36px;top:40px;font-size:15px}
.letterhead .wordmark .dot{width:9px;height:9px}
.letterhead .band .rule-v{left:266px;top:27px;height:55px;background:var(--blue)}
.letterhead .addr{position:absolute;left:282px;top:27px;font-size:6.8px;line-height:8.5px}
.letterhead .contact{position:absolute;left:282px;top:48px;font-size:6.8px;line-height:8.8px}
.letterhead .contact svg{width:6px;height:6px;margin-right:4px}
.letter{position:absolute;left:35px;top:157px;width:325px;color:var(--body)}
.letter .salute{font-family:"Montserrat",sans-serif;font-weight:300;font-size:10px;color:#555;margin-bottom:17px}
.letter p{font-family:"Montserrat",sans-serif;font-weight:300;font-size:5.5px;line-height:8.5px;margin-bottom:8.5px;text-align:justify}
.letter .closing{margin-top:14px}
.signature{position:absolute;left:33px;top:390px;width:70px;height:30px;background:linear-gradient(90deg,#dbeaf5,#eef6fb);border-radius:3px}
.letterhead .motto{position:absolute;left:0;right:0;top:514px;text-align:center;font-size:14px;color:#333}

/* envelope */
.env-back{left:490px;top:47px;width:354px;height:160px;background:var(--ink)}
.env-back .flap-inner{position:absolute;left:6px;right:6px;top:0;height:60px;background:var(--blue);border-radius:0 0 16px 16px}
.env-back .motto{position:absolute;left:0;right:0;top:33px;text-align:center;font-size:9.5px;color:var(--white)}
.env-back .wordmark{position:absolute;left:50%;top:11px;transform:translateX(-50%);font-size:11px}
.env-back .wordmark .dot{width:7px;height:7px}
.env-front{left:543px;top:132px;width:356px;height:161px;background:var(--ink);box-shadow:0 1px 3px rgba(0,0,0,.35)}
.env-front .wordmark{position:absolute;left:20px;top:45px;font-size:12px}
.env-front .wordmark .dot{width:7px;height:7px}
.env-front .addr{position:absolute;left:20px;top:63px;font-size:7px;line-height:9.3px}

/* business cards */
.card-front{left:944px;top:48px;width:186px;height:106px;background:var(--white)}
.card-front .who{position:absolute;right:90px;top:43px;text-align:right;color:#666;font-size:3.8px;line-height:5.4px}
.card-front .who .name{font-size:5.6px;line-height:7px;font-weight:700}
.card-front .rule-v{left:100px;top:44px;height:22px;background:var(--blue)}
.card-front .contact{position:absolute;left:105px;top:44px;color:#666;font-size:3.8px;line-height:5.4px}
.card-front .contact svg{width:3px;height:3px;margin-right:3px}
.card-back{left:944px;top:182px;width:192px;height:110px;background:var(--ink)}
.card-back .wordmark{position:absolute;left:50%;top:45px;transform:translateX(-50%);font-size:14px}
.card-back .wordmark .dot{width:8px;height:8px}
.card-back .motto{position:absolute;left:0;right:0;top:84px;text-align:center;font-size:9px}

/* email signatures */
.sig{background:var(--ink)}
.sig-1{left:490px;top:335px;width:175px;height:265px}
.sig-1 .wordmark{position:absolute;left:28px;top:69px;font-size:18px}
.sig-1 .wordmark .dot{width:10px;height:10px}
.sig-1 .name{position:absolute;left:27px;top:107px;font-size:15px}
.sig-1 .role{position:absolute;left:27px;top:126px;font-size:8.5px}
.sig-1 .dash{position:absolute;left:28px;width:14px;height:1px;background:rgba(255,255,255,.5)}
.sig-1 .dash.blue{background:var(--blue)}
.sig-1 .addr{position:absolute;left:28px;top:152px;font-size:8.8px;line-height:11.4px}
.sig-1 .contact{position:absolute;left:28px;top:193px;font-size:8.8px;line-height:11.4px}
.sig-1 .contact svg{width:7px;height:7px;margin-right:5px}

.sig-2{left:695px;top:335px;width:455px;height:141px}
.sig-2 .wordmark{position:absolute;left:38px;top:60px;font-size:18px}
.sig-2 .wordmark .dot{width:10px;height:10px}
.sig-2 .rule-v.a{left:139px;top:47px;height:50px}
.sig-2 .rule-v.b{left:297px;top:47px;height:50px}
.sig-2 .name{position:absolute;left:162px;top:43px;font-size:15px}
.sig-2 .details{position:absolute;left:162px;top:61px;font-size:9px;line-height:11.4px}
.sig-2 .details .gap{height:3px}
.sig-2 .contact{position:absolute;left:318px;top:49px;font-size:9px;line-height:11.4px}
.sig-2 .contact svg{width:7px;height:7px;margin-right:5px}

.sig-3{left:695px;top:513px;width:455px;height:87px}
.sig-3 .wordmark{position:absolute;left:18px;top:36px;font-size:16px}
.sig-3 .wordmark .dot{width:9px;height:9px}
.sig-3 .rule-v.a{left:101px;top:29px;height:30px}
.sig-3 .rule-v.b{left:211px;top:29px;height:30px}
.sig-3 .rule-v.c{left:334px;top:29px;height:30px}
.sig-3 .who{position:absolute;left:106px;width:100px;top:33px;text-align:center}
.sig-3 .who .name{font-size:13.5px;line-height:15px}
.sig-3 .who .role{font-size:9px;line-height:11px}
.sig-3 .details{position:absolute;left:226px;top:27px;font-size:9px;line-height:11.6px}
.sig-3 .contact{position:absolute;left:350px;top:27px;font-size:9px;line-height:11.6px}
.sig-3 .contact svg{width:7px;height:7px;margin-right:5px}
</style>
</head>
<body>

<svg width="0" height="0" style="position:absolute" aria-hidden="true">
  <symbol id="i-phone" viewBox="0 0 10 10"><path d="M2.2 0.6l1.6 2.2-1 1.1c.6 1.3 1.6 2.3 2.9 2.9l1.1-1 2.2 1.6-.9 1.9C4.5 9.2.8 5.5.3 1.5z"/></symbol>
  <symbol id="i-mobile" viewBox="0 0 10 10"><path d="M2.5 0h5v10h-5zM3.4 1v7h3.2V1z"/></symbol>
  <symbol id="i-mail" viewBox="0 0 10 10"><path d="M0 2h10v6H0zM1 3l4 3 4-3z"/></symbol>
  <symbol id="i-globe" viewBox="0 0 10 10"><circle cx="5" cy="5" r="4.6"/><path d="M5 .6v8.8M.6 5h8.8" stroke="#1e1e20" stroke-width=".8"/></symbol>
</svg>

<!-- Letterhead -->
<section class="piece letterhead">
  <header class="band">
    <div class="wordmark"><span class="dot"></span>Vale 8</div>
    <div class="rule-v"></div>
    <div class="addr">412 Birchwood Lane<br>Atlanta, Georgia 30309</div>
    <ul class="contact">
      <li><svg><use href="#i-phone"/></svg>555-214-7730</li>
      <li><svg><use href="#i-mobile"/></svg>555-318-4462</li>
      <li><svg><use href="#i-mail"/></svg>info@vale8.com</li>
      <li><svg><use href="#i-globe"/></svg>www.vale8.com</li>
    </ul>
  </header>
  <div class="letter">
    <div class="salute">Dear Mr. Hart,</div>
    <p>Lorem ipsum dolor sit amet, consectetur adipiscing elit. Donec orci purus, luctus vitae dignissim eu, iaculis sed purus. Vivamus faucibus, ipsum nec aliquet viverra, leo mauris condimentum ligula, sit amet sagittis enim ligula quis arcu. Nam egestas tortor id nisi porttitor mattis. In tortor ante, ultricies in suscipit a, tempus non massa. Vivamus et auctor mi. Fusce vel massa nulla. Phasellus nec eros mauris, et scelerisque orci.</p>
    <p>Donec malesuada orci vitae nulla accumsan porta a id massa. Quisque accumsan iaculis magna sit amet fringilla. Maecenas consequat, magna eget tincidunt semper, odio nibh rutrum mi, id feugiat ante nisi eu risus. Vestibulum nunc orci, rhoncus a placerat in, ultricies in mi. Cras mattis varius eros, vel fringilla nisi suscipit eget. Quisque scelerisque sagittis nulla at porttitor.</p>
    <p>Sed id augue vitae urna euismod commodo aliquet a quam. Pellentesque arcu velit, cursus et malesuada ut, consequat et diam. Nullam erat sem, rhoncus id ullamcorper vitae, rhoncus et arcu. In ultricies ultricies nulla, ut rutrum nisi iaculis at. Donec eu magna a metus ornare faucibus. Fusce aliquet faucibus ultricies. Morbi semper, est id tincidunt gravida, sem arcu adipiscing lacus, ac bibendum nulla leo eu purus. Quisque nec diam sed risus consectetur a ccumsan quis quis nibh. Vestibulum id purus lorem.</p>
    <p>It is a long established fact that a reader will be distracted by the readable content of a page when looking at its layout. The point of using Lorem Ipsum is that it has a more-or-less normal distribution of letters, as opposed to using 'Content here, content here', making it look like readable English. Many desktop publishing packages</p>
    <p class="closing">Sincerely,</p>
  </div>
  <div class="signature" role="img" aria-label="Handwritten signature of Daniel Hart"></div>
  <div class="motto script">Keep More of What You Build</div>
</section>
<div class="label" style="left:269px;top:619px">LETTERHEAD</div>

<!-- Envelope -->
<section class="piece env-back">
  <div class="flap-inner"></div>
  <div class="wordmark"><span class="dot" style="background:var(--white)"></span>Vale 8</div>
  <div class="motto script">Keep More of What You Build</div>
</section>
<section class="piece env-front">
  <div class="wordmark"><span class="dot"></span>Vale 8</div>
  <div class="addr">412 Birchwood Lane<br>Atlanta, Georgia 30309</div>
</section>
<div class="label" style="left:723px;top:303px">ENVELOPE</div>

<!-- Business cards -->
<section class="piece card-front">
  <div class="who"><div class="name">DANIEL HART</div>President<br>412 Birchwood Lane<br>Atlanta, Georgia 30309</div>
  <div class="rule-v"></div>
  <ul class="contact">
    <li><svg><use href="#i-phone"/></svg>555-214-7730</li>
    <li><svg><use href="#i-mobile"/></svg>555-907-2215</li>
    <li><svg><use href="#i-mail"/></svg>info@vale8.com</li>
    <li><svg><use href="#i-globe"/></svg>www.vale8.com</li>
  </ul>
</section>
<div class="label" style="left:1040px;top:163px">FRONT CARD</div>
<section class="piece card-back">
  <div class="wordmark"><span class="dot"></span>Vale 8</div>
  <div class="motto script">Keep More of What You Build</div>
</section>
<div class="label" style="left:1040px;top:303px">BACK CARD</div>

<!-- Email signature 1 -->
<section class="piece sig sig-1">
  <div class="wordmark"><span class="dot"></span>Vale 8</div>
  <div class="name">Daniel Hart</div>
  <div class="role">President</div>
  <div class="dash" style="top:145px"></div>
  <div class="addr">412 Birchwood Lane<br>Atlanta, Georgia 30309</div>
  <div class="dash blue" style="top:183px"></div>
  <ul class="contact">
    <li><svg><use href="#i-phone"/></svg>555-214-7730</li>
    <li><svg><use href="#i-mobile"/></svg>555-318-4462</li>
    <li><svg><use href="#i-mail"/></svg>info@vale8.com</li>
    <li><svg><use href="#i-globe"/></svg>www.vale8.com</li>
  </ul>
</section>
<div class="label" style="left:581px;top:619px">EMAIL SIGNATURE 1</div>

<!-- Email signature 2 -->
<section class="piece sig sig-2">
  <div class="wordmark"><span class="dot"></span>Vale 8</div>
  <div class="rule-v a"></div>
  <div class="name">Daniel Hart</div>
  <div class="details">President<div class="gap"></div>412 Birchwood Lane<br>Atlanta, Georgia 30309</div>
  <div class="rule-v b"></div>
  <ul class="contact">
    <li><svg><use href="#i-phone"/></svg>555-214-7730</li>
    <li><svg><use href="#i-mobile"/></svg>555-318-4462</li>
    <li><svg><use href="#i-mail"/></svg>info@vale8.com</li>
    <li><svg><use href="#i-globe"/></svg>www.vale8.com</li>
  </ul>
</section>
<div class="label" style="left:909px;top:486px">EMAIL SIGNATURE 2</div>

<!-- Email signature 3 -->
<section class="piece sig sig-3">
  <div class="wordmark"><span class="dot"></span>Vale 8</div>
  <div class="rule-v a"></div>
  <div class="who"><div class="name">Daniel Hart</div><div class="role">President</div></div>
  <div class="rule-v b"></div>
  <div class="details">412 Birchwood Lane<br>Atlanta, Georgia 30309<br>www.vale8.com</div>
  <div class="rule-v c"></div>
  <ul class="contact">
    <li><svg><use href="#i-phone"/></svg>555-214-7730</li>
    <li><svg><use href="#i-mobile"/></svg>555-318-4462</li>
    <li><svg><use href="#i-mail"/></svg>info@vale8.com</li>
  </ul>
</section>
<div class="label" style="left:909px;top:619px">EMAIL SIGNATURE 3</div>

</body>
</html>
```